Health Clinic treating people with mental illness needs a website

We need a website for a new mental health clinic based in Florida called Solvane Wellness USA. We treat people with mental health issues such as depression, PTSD, Bipolar, chronic pain, etc. I want the website to be easy to follow and inviting to the visitors. It should be easy to locate the different treatment options and how to go about contacting and making appointments. The images on the website should be something that the patients can relate to, whether a close up of a woman's face, something that conveys emotion. The patients visiting this website are often sad and miserable, they need to be able to feel comfortable when they look at this website. I want them to feel that we understand where they are coming from. I like colors such as purple, turquoise, lavender.

Target Market(s)

College students, veterans, anyone with mental illness

Industry/Entity Type

Health And Wellness

Font styles to use
Serif
Sans Serif

Colors

Designer to choose colors to be used in the design.

Requirements
Must have
• There should be a home/landing page, about us page, treatment page, contact page, and a FAQ page. I've included my logo below.
Nice to have
• The flow of the web pages should be calming and welcoming. I want people to feel warm and understood when they enter our page.
Should not have
• The images and writing should not be overly stimulating or aggressive.

```html
<!DOCTYPE html>
<html lang="en">
<head>
<meta charset="utf-8">
<title>Solvane Wellness USA</title>
<link href="https://fonts.googleapis.com/css2?family=Open+Sans:wght@400;600;700&family=Roboto+Slab:wght@400;700&display=swap" rel="stylesheet">
<style>
:root{
  --purple:#8c2a89;
  --purple-soft:rgba(140,42,137,.86);
  --teal:#2eae95;
  --teal-soft:rgba(46,174,149,.92);
  --ink:#333;
  --muted:#777;
  --line:#e4e4e4;
  --grey:#f2f2f2;
  --dark:#1c1c1c;
  --white:#fff;
}
*{box-sizing:border-box;margin:0;padding:0}
html,body{width:1200px;height:4352px;overflow:hidden}
body{position:relative;font-family:"Open Sans",Arial,sans-serif;color:var(--ink);background:var(--white)}
h2.section-title{position:absolute;left:0;width:1200px;text-align:center;font-family:"Roboto Slab",Georgia,serif;font-weight:400;font-size:40px;line-height:1.2;color:var(--ink)}
h2.section-title span{color:var(--purple)}
.btn{display:inline-block;font-size:15px;line-height:1.2;color:var(--white);padding:12px 26px;border-radius:2px}
.btn.purple{background:var(--purple)}
.btn.teal{background:var(--teal)}
.photo{position:absolute}
p{line-height:1.75}

/* header */
.site-header{position:absolute;left:0;top:0;width:1200px;height:144px}
.brand{position:absolute;left:112px;top:50px;display:flex;align-items:center;gap:14px}
.brand-dot{width:22px;height:22px;border-radius:50%;background:var(--purple)}
.brand-name{font-weight:700;font-size:30px;color:var(--purple)}
.call{position:absolute;right:112px;top:30px;font-weight:700;font-size:20px;color:var(--purple)}
.nav{position:absolute;right:100px;top:90px;display:flex;gap:42px;font-size:16px}
.nav a{color:var(--ink);text-decoration:none;position:relative}
.nav a.active{color:var(--purple)}
.nav a.active:before{content:"";position:absolute;left:50%;top:-30px;width:14px;height:14px;margin-left:-7px;border-radius:50%;background:var(--purple)}

/* hero */
.hero-photo{left:0;top:144px;width:1200px;height:728px;background:linear-gradient(100deg,#c9dbe6 0%,#e8eef2 35%,#d7c8c4 55%,#eef0f2 75%,#c7d3e0 100%)}
.hero-card{position:absolute;left:640px;top:500px;width:448px;height:260px;background:var(--purple-soft);color:var(--white);padding:40px 44px}
.hero-card h1{font-family:"Roboto Slab",Georgia,serif;font-weight:400;font-size:34px;line-height:1.2;margin-bottom:12px}
.hero-card p{font-size:15px;margin-bottom:18px}

/* treatments */
.card{position:absolute;top:1020px;width:304px;height:468px;border:1px solid var(--line);background:var(--white)}
.card .photo{left:0;top:0;width:302px;height:228px}
.card-head{position:absolute;left:16px;right:16px;top:248px;display:flex;justify-content:space-between;font-size:19px}
.card-head .price{color:var(--purple)}
.card p{position:absolute;left:16px;right:16px;top:296px;font-size:13px;color:var(--muted)}
.card .btn{position:absolute;left:16px;top:412px;padding:9px 20px;font-size:13px}

/* appointment band */
.band-photo{left:0;top:1580px;width:1200px;height:508px;background:linear-gradient(90deg,#f3f4f2 0%,#e7e4e0 45%,#d9c3b6 65%,#ebe2dc 100%)}
.band-box{position:absolute;left:112px;top:1580px;width:396px;height:480px;background:var(--teal-soft);color:var(--white);padding:40px 36px}
.band-box h3{font-family:"Roboto Slab",Georgia,serif;font-weight:400;font-size:24px;line-height:1.4;margin-bottom:22px}
.band-box p{font-size:13px;margin-bottom:26px}

/* about */
.about-text{position:absolute;left:150px;top:2250px;width:900px;text-align:center;font-size:14px;color:var(--muted)}
.about-btn{position:absolute;left:518px;top:2370px;width:164px;text-align:center}

/* testimonials */
.testi-box{position:absolute;left:0;top:2488px;width:488px;height:472px;background:var(--purple);color:var(--white);padding:40px 112px 0 112px}
.testi-box .kicker{font-size:18px}
.testi-box h3{font-family:"Roboto Slab",Georgia,serif;font-weight:400;font-size:34px;line-height:1.2;margin-bottom:20px}
.testi-box p{font-size:13px;margin-bottom:26px}
.testi-photo{left:488px;top:2488px;width:712px;height:472px;background:linear-gradient(90deg,#8f7a6c 0%,#c8bfb8 40%,#d6d2cf 70%,#7f8c9c 100%)}

/* gallery */
.sub{position:absolute;left:0;width:1200px;text-align:center;font-size:13px;color:var(--muted)}
.g{top:3140px;width:236px;height:240px}

/* contact */
.contact{position:absolute;left:0;top:3460px;width:1200px;height:472px;background:var(--grey)}
.map{left:160px;top:3600px;width:492px;height:280px;background:linear-gradient(135deg,#e9e6dc 0%,#d8e4d0 50%,#b9d3e6 100%)}
.form{position:absolute;left:668px;top:3600px;width:380px}
.field{height:34px;border:1px solid #ddd;background:var(--white);font-size:12px;line-height:1.2;color:#999;padding:9px 12px;margin-bottom:8px}
.field.message{height:110px}
.form .btn{padding:10px 26px;font-size:13px}

/* footer */
.site-footer{position:absolute;left:0;top:3932px;width:1200px;height:420px;background:var(--dark);color:var(--white)}
.news-title{position:absolute;left:152px;top:78px;font-family:"Roboto Slab",Georgia,serif;font-size:26px;font-weight:400;line-height:1.2}
.news-form{position:absolute;left:152px;top:170px;display:flex}
.news-input{width:352px;height:48px;background:var(--white);color:#999;font-size:13px;padding:14px}
.news-btn{width:100px;height:48px;background:var(--teal);font-size:13px;text-align:center;line-height:48px}
.social{position:absolute;left:720px;top:78px;display:flex;gap:10px}
.social span{width:34px;height:34px;border:1px solid #aaa;border-radius:50%}
.contact-info{position:absolute;left:720px;top:140px;font-size:13px;line-height:2.2;color:#ddd}
.copy{position:absolute;left:0;bottom:26px;width:1200px;text-align:center;font-size:12px;color:#bbb}
</style>
</head>
<body>

<header class="site-header">
  <div class="brand"><span class="brand-dot"></span><span class="brand-name">Solvane Wellness USA</span></div>
  <div class="call">Call Us : 000-555-0147</div>
  <nav class="nav">
    <a class="active" href="#">Home</a><a href="#">About us</a><a href="#">Treatment</a><a href="#">FAQ</a><a href="#">Contact us</a>
  </nav>
</header>

<div class="photo hero-photo" role="img" aria-label="Photo of a distressed young woman sitting with a caring female doctor at a clinic desk"></div>
<div class="hero-card">
  <h1>Solvane Wellness</h1>
  <p>Sed ut perspiciatis unde omnis iste natus error sit voluptatem accusantium doloremque laudantium.</p>
  <span class="btn teal">Read More</span>
</div>

<h2 class="section-title" style="top:930px">Our <span>Treatment</span></h2>

<div class="card" style="left:112px">
  <div class="photo" role="img" aria-label="Photo of a woman sitting alone by a window, feeling low" style="background:linear-gradient(135deg,#d8cfc6,#a99182)"></div>
  <div class="card-head"><span>Depression</span><span class="price">$20.99</span></div>
  <p>Sed ut perspiciatis unde omnis iste natus error sit voluptatem accusantium doloremque laudantium, totam rem aperiam, eaque ipsa quae.</p>
  <span class="btn purple">Read More</span>
</div>
<div class="card" style="left:444px">
  <div class="photo" role="img" aria-label="Photo of a woman holding her neck in pain" style="background:linear-gradient(135deg,#efe9e4,#c9b8ac)"></div>
  <div class="card-head"><span>Chronic pain</span><span class="price">$20.99</span></div>
  <p>Sed ut perspiciatis unde omnis iste natus error sit voluptatem accusantium doloremque laudantium, totam rem aperiam, eaque ipsa quae.</p>
  <span class="btn teal">Read More</span>
</div>
<div class="card" style="left:776px">
  <div class="photo" role="img" aria-label="Photo of a woman with dark hair covering her face in distress" style="background:linear-gradient(135deg,#6a5a55,#2d2624)"></div>
  <div class="card-head"><span>Bipolar</span><span class="price">$20.99</span></div>
  <p>Sed ut perspiciatis unde omnis iste natus error sit voluptatem accusantium doloremque laudantium, totam rem aperiam, eaque ipsa quae.</p>
  <span class="btn purple">Read More</span>
</div>

<div class="photo band-photo" role="img" aria-label="Photo of a doctor taking notes beside an older female patient"></div>
<div class="band-box">
  <h3>Sed ut perspiciatis unde omnis iste natus error sit voluptatem.</h3>
  <p>Sed ut perspiciatis unde omnis iste natus error sit voluptatem accusantium doloremque laudantium, totam rem aperiam, eaque ipsa quae ab illo inventore veritatis et quasi architecto beatae vitae dicta sunt explicabo. Nemo enim ipsam voluptatem quia voluptas sit aspernatur.</p>
  <span class="btn purple">Book Appointment</span>
</div>

<h2 class="section-title" style="top:2172px">About Our <span>Solvane Wellness</span></h2>
<p class="about-text">Sed ut perspiciatis unde omnis iste natus error sit voluptatem accusantium doloremque laudantium, totam rem aperiam, eaque ipsa quae ab illo inventore veritatis et quasi architecto beatae vitae dicta sunt explicabo. Nemo enim ipsam voluptatem quia voluptas sit aspernatur aut odit aut fugit, sed quia consequuntur magni dolores eos qui ratione voluptatem sequi nesciunt.</p>
<span class="btn teal about-btn">Read More</span>

<div class="testi-box">
  <div class="kicker">Customer</div>
  <h3>Testimonials</h3>
  <p>Sed ut perspiciatis unde omnis iste natus error sit voluptatem accusantium doloremque laudantium, totam rem aperiam, eaque ipsa quae ab illo inventore veritatis et quasi architecto beatae vitae dicta sunt explicabo. Nemo enim ipsam voluptatem quia voluptas sit aspernatur aut odit aut fugit sed.</p>
  <span class="btn teal">Read More</span>
</div>
<div class="photo testi-photo" role="img" aria-label="Photo of a counselling session with two women talking in a bright living room"></div>

<h2 class="section-title" style="top:3020px">Photo <span>Gallery</span></h2>
<p class="sub" style="top:3086px">Sed ut perspiciatis unde omnis iste natus error sit voluptatem accusantium doloremque laudantium.</p>
<div class="photo g" style="left:112px;background:linear-gradient(135deg,#b7c4cf,#e4d8c8)" role="img" aria-label="Photo of a therapist talking with a patient on a sofa"></div>
<div class="photo g" style="left:360px;background:linear-gradient(135deg,#5b4d48,#c7b6a6)" role="img" aria-label="Photo of a group therapy circle"></div>
<div class="photo g" style="left:608px;background:linear-gradient(135deg,#e9ddd8,#b79a8e)" role="img" aria-label="Photo of a young woman in a counselling session"></div>
<div class="photo g" style="left:852px;background:linear-gradient(135deg,#c9d6d2,#8f9d9a)" role="img" aria-label="Photo of a doctor consulting with a patient"></div>

<section class="contact">
  <h2 class="section-title" style="top:44px">Contact <span>Us</span></h2>
  <p class="sub" style="top:104px">Sed ut perspiciatis unde omnis iste natus error sit voluptatem accusantium doloremque laudantium.</p>
</section>
<div class="photo map" role="img" aria-label="Map of the clinic locations around Tampa Bay"></div>
<div class="form">
  <div class="field">Name</div>
  <div class="field">Email</div>
  <div class="field">Phone</div>
  <div class="field message">Message</div>
  <span class="btn purple">SUBMIT</span>
</div>

<footer class="site-footer">
  <h3 class="news-title">Subscribe to Our Newsletter</h3>
  <div class="news-form"><div class="news-input">Email</div><div class="news-btn">Subscribe</div></div>
  <div class="social"><span></span><span></span><span></span></div>
  <div class="contact-info">
    hello@solvanewellness.com&nbsp;&nbsp;000-555-0147<br>
    Suite 12 Harbor Lane, Tampa, FL 33602
  </div>
  <div class="copy">© Copyright 2019 Solvane Wellness All rights reserved</div>
</footer>

</body>
</html>
```